The Velvet Easel Co - Photos to Custom Oil Paintings

We need a website and logo designed and built allowing customers to purchase custom oil paintings. The paintings will come from a customers single photograph or even combination of photos. They will be able to complete a straight forward checkout process, selecting their desired medium (oil or charcoal painting), their desired size, the number of figures in the painting, the type of background required (as per photo or let the artist decide). Which will then automaticaly provide the customer with a price for the purchase. Allowing them to add a photo to the order which they can then submit with the order present in their personal account etc etc etc.
Theres one website in particular that i will be competing with. That is based in the US - http://www.brushmorrow.com
I wish to far exceed the appearence of the already present site.
At the moment i wish to include Coinvale in the payment process. Unless there are some cheaper, more cost efficient ways, please let me know.
The company name is The Velvet Easel Co. Domain has been purchased - www.thevelveteasel.co (via Hostlark - Linux)
I have no great sense of design, but the site must be straight forward, eye catching, engaging and give the customer a sense of high quality. Some kind of flash animation with pictures on the front page scrolling?
For myself, the admin side, ideally must be straight forward to maintain. The ability to update customers accounts with info (they will then be informed there is an update in their account etc)
The ability for automated emails from point of sale (sales orders with generated order numbers) to myself. Again automated emails to the customers once the "status" of their order or other information has been submitted to their account (by myself) or a similar system.
Updates
All,
Please note, the budget is able to increase subject to what additional work is needed. As far as the admin area goes. I am open to suggestions to ensure ease of use and efficiency.
Any questions, comments or ideas are fully welcomed.
Many thanks,
Dan Holloway
Industry/Entity Type
It Company
Logo Text
Logo styles of interest
Pictorial/Combination Logo
Abstract Logo
Wordmark Logo
Lettermark Logo
Look and feel
Each slider illustrates characteristics of the customer's brand and the style your logo design should communicate.

```html
<!DOCTYPE html>
<html lang="en">
<head>
<meta charset="utf-8">
<title>The Velvet Easel – Oil Painting From Photo</title>
<link rel="stylesheet" href="https://fonts.googleapis.com/css2?family=Arimo:wght@400;700&family=Didact+Gothic&display=swap">
<style>
  :root {
    --wall-back: #5a3114;
    --text-light: #ffffff;
    --text-soft: #f1e6d6;
    --nav-text: #dcc7ab;
    --lamp: #a45a2c;
    --dot: #3a1d0b;
    --dot-active: #1e0e04;
    --button: #9c7448;
    --button-text: #3b230f;
    --autumn-deep: #8a3a12;
    --autumn-warm: #d2761e;
    --autumn-light: #e8b45a;
    --gift-red: #c8202a;
  }
  * { margin: 0; padding: 0; box-sizing: border-box; }
  html, body { width: 1200px; height: 840px; overflow: hidden; }
  body {
    position: relative;
    background: var(--wall-back);
    font-family: "Arimo", Arial, sans-serif;
    color: var(--text-light);
  }
  .room { position: absolute; inset: 0; }

  .account-links {
    position: absolute; top: 17px; right: 32px;
    font-size: 13px; color: var(--text-light);
    display: flex; align-items: center; gap: 6px;
  }

  .brand {
    position: absolute; left: 57px; top: 126px;
    display: flex; align-items: center; gap: 12px;
  }
  .brand-dot { width: 16px; height: 16px; border-radius: 50%; background: var(--text-light); flex: none; }
  .brand-name { font-size: 28px; font-weight: 700; color: var(--text-light); white-space: nowrap; }

  .main-nav { position: absolute; left: 143px; top: 251px; list-style: none; }
  .main-nav li { height: 36px; font-size: 15px; font-weight: 700; color: var(--nav-text); letter-spacing: 0.3px; white-space: nowrap; }

  .search {
    position: absolute; left: 143px; top: 590px; width: 177px; height: 34px;
    border-radius: 10px; background: #3a1e0c;
    box-shadow: inset 0 2px 4px rgba(0,0,0,.6), 0 1px 0 rgba(255,255,255,.12);
  }
  .search svg { position: absolute; right: 10px; top: 7px; }

  .lamp {
    position: absolute; top: 50px; width: 84px; height: 7px;
    background: var(--lamp); border-radius: 2px;
  }
  .lamp::after {
    content: ""; position: absolute; left: -28px; top: 4px; width: 140px; height: 60px;
    background: radial-gradient(ellipse at top, rgba(255,220,170,.28), transparent 70%);
  }
  .showcase-label {
    position: absolute; top: 86px; font-family: "Didact Gothic", Arial, sans-serif;
    font-size: 15px; color: var(--text-light); text-align: center; width: 240px;
  }
  .showcase-frame {
    position: absolute; top: 115px; height: 316px; border: 6px solid #fff;
    box-shadow: 0 4px 10px rgba(0,0,0,.4);
  }
  .showcase-frame.photo { left: 458px; width: 275px;
    background: linear-gradient(180deg, var(--autumn-warm) 0%, var(--autumn-deep) 55%, #6b4a2a 100%); }
  .showcase-frame.painting { left: 853px; width: 297px;
    background: radial-gradient(ellipse at 50% 35%, var(--autumn-light) 0%, var(--autumn-warm) 35%, var(--autumn-deep) 75%, #5d4226 100%); }

  .slider-dots { position: absolute; top: 465px; left: 984px; display: flex; gap: 21px; }
  .slider-dots span { width: 16px; height: 16px; border-radius: 50%; background: var(--dot); box-shadow: inset 0 1px 2px rgba(0,0,0,.5); }
  .slider-dots span.active { background: var(--dot-active); }

  .intro { position: absolute; left: 463px; top: 488px; width: 700px; }
  .intro h1 {
    font-family: "Didact Gothic", Arial, sans-serif; font-weight: 400;
    font-size: 22px; letter-spacing: 0.3px; color: var(--text-light);
  }
  .intro p { margin-top: 16px; font-size: 14px; line-height: 36px; color: var(--text-soft); }

  .learn-more {
    position: absolute; left: 1044px; top: 696px; width: 116px; height: 30px;
    border-radius: 9px; background: linear-gradient(180deg, #b38a5c, var(--button));
    font-family: "Didact Gothic", Arial, sans-serif; font-size: 14px; color: var(--button-text);
    display: flex; align-items: center; justify-content: center;
    box-shadow: 0 2px 4px rgba(0,0,0,.4);
  }

  .gift-badge {
    position: absolute; left: 258px; top: 771px; width: 126px; height: 60px;
    background: #fff; border-radius: 5px; display: flex; align-items: center; gap: 3px; padding: 4px;
  }
  .gift-ribbon { width: 30px; height: 44px; background: var(--gift-red); border-radius: 3px; flex: none; }
  .gift-text { font-size: 9.5px; color: #333; line-height: 1.35; text-align: center; white-space: nowrap; flex: 1; }
  .gift-text strong { display: block; color: var(--gift-red); font-size: 11px; font-weight: 400; }

  .payment-badge {
    position: absolute; left: 396px; top: 782px; width: 126px; height: 37px;
    background: #fff; border: 1px solid #bbb; display: flex; flex-direction: column; align-items: center; padding-top: 3px;
  }
  .payment-badge .name { font-size: 12px; font-weight: 700; color: #2b4f8a; }
  .payment-badge .cards { display: flex; gap: 3px; margin-top: 3px; }
  .payment-badge .cards span { width: 22px; height: 12px; background: #c9ced6; border-radius: 2px; }

  .social { position: absolute; left: 532px; top: 781px; display: flex; gap: 10px; }
  .social span {
    width: 38px; height: 38px; border-radius: 5px; background: linear-gradient(180deg, #e8e8e8, #9d9d9d);
    color: #444; font-size: 7px; font-weight: 700; display: flex; align-items: center; justify-content: center;
  }

  .copyright { position: absolute; left: 864px; top: 820px; font-size: 12.5px; color: var(--text-light); white-space: nowrap; }
</style>
</head>
<body>
  <svg class="room" width="1200" height="840" viewBox="0 0 1200 840" aria-hidden="true">
    <defs>
      <radialGradient id="backWall" cx="0.55" cy="0.35" r="0.7">
        <stop offset="0" stop-color="#7a4620"/>
        <stop offset="1" stop-color="#4f2a10"/>
      </radialGradient>
      <linearGradient id="sideWall" x1="0" y1="0" x2="1" y2="0">
        <stop offset="0" stop-color="#2f170a"/>
        <stop offset="0.6" stop-color="#4a2711"/>
        <stop offset="1" stop-color="#3d200d"/>
      </linearGradient>
    </defs>
    <rect width="1200" height="840" fill="url(#backWall)"/>
    <polygon points="0,0 258,0 402,56 402,708 0,840" fill="url(#sideWall)"/>
    <polygon points="258,0 1200,0 1200,6 402,56" fill="#d8d2c4"/>
    <line x1="402" y1="56" x2="402" y2="708" stroke="#2a1508" stroke-width="2"/>
    <polygon points="0,840 402,708 1200,770 1200,840" fill="#2a1208"/>
    <line x1="0" y1="840" x2="402" y2="708" stroke="#1a0a03" stroke-width="2"/>
    <line x1="402" y1="708" x2="1200" y2="770" stroke="#1a0a03" stroke-width="2"/>
  </svg>

  <div class="account-links">
    <span>My Account | Shopping Cart</span>
    <svg width="18" height="14" viewBox="0 0 18 14"><path d="M1 1h3l2 8h9l2-6H5" fill="none" stroke="#fff" stroke-width="1.6"/><circle cx="7" cy="12" r="1.4" fill="#fff"/><circle cx="14" cy="12" r="1.4" fill="#fff"/></svg>
  </div>

  <div class="brand">
    <div class="brand-dot"></div>
    <div class="brand-name">The Velvet Easel</div>
  </div>

  <ul class="main-nav">
    <li>HOW IT WORKS</li>
    <li>ORDER YOUR PAINTING</li>
    <li>GALLERIES</li>
    <li>GIFT IDEAS</li>
    <li>TESTIMONIALS</li>
    <li>FAQ</li>
    <li>PRICES</li>
    <li>GUARANTEE</li>
    <li>CONTACT US</li>
  </ul>

  <div class="search">
    <svg width="20" height="20" viewBox="0 0 20 20"><circle cx="8" cy="8" r="5.5" fill="none" stroke="#e8dccb" stroke-width="2.4"/><line x1="12" y1="12" x2="18" y2="18" stroke="#e8dccb" stroke-width="3" stroke-linecap="round"/></svg>
  </div>

  <div class="lamp" style="left:554px"></div>
  <div class="lamp" style="left:961px"></div>
  <div class="showcase-label" style="left:476px">ORIGINAL PHOTO</div>
  <div class="showcase-label" style="left:883px">PORTRAIT PAINTING</div>

  <div class="showcase-frame photo" role="img" aria-label="Customer photo of an autumn tree-lined path"></div>
  <div class="showcase-frame painting" role="img" aria-label="Oil painting of the same autumn tree-lined path"></div>

  <div class="slider-dots"><span class="active"></span><span></span><span></span><span></span><span></span></div>

  <section class="intro">
    <h1>OIL PAINTING FROM PHOTO</h1>
    <p>What types of oil paintings from photos do we do? The Velvet Easel can do an oil painting from photo using any type of photo you have. For example we can use your wedding photos, family photos, pet photos, landscape photos, children photos, dog photos, cat photos, house photos, all of which can be made into an oil painting from photo. Below you can see different types of oil paintings from photos we have done for past customers.</p>
  </section>

  <div class="learn-more">LEARN MORE</div>

  <div class="gift-badge">
    <div class="gift-ribbon" role="img" aria-label="Gift ribbon"></div>
    <div class="gift-text">Get our special<strong>Gift certificate</strong>for your loved ones</div>
  </div>

  <div class="payment-badge">
    <div class="name">Coinvale</div>
    <div class="cards"><span></span><span></span><span></span><span></span></div>
  </div>

  <div class="social"><span>Pinwall</span><span>Chirpline</span><span>ReelHub</span></div>

  <div class="copyright">Copyright © 2012 The Velvet Easel, All rights reserved</div>
</body>
</html>
```